Company or website name
- Velmira, LLC
- Velmira, LLC
- Describe your company and organization and target audience
- Velmira, LLC is a research, science and technology based manufacturing company that formulates, develops, manufactures and packages a full complement of personal care products for domestic and international concerns. We private label and contract package personal care products, cosmetics, bath salts and powders and home fragrance products. Velmira is conveniently located in Southern California adjacent to major transportation hubs and international airports. We utilize earth friendly, green manufacturing processes, maximize the use of renewable resource raw materials and minimize the use of non-renewable and petrochemical based raw materials. We provide formulation and product development services with low minimum order quantities and short lead times. Velmira is the intersection between nature, science, beauty and innovation. We are a B-2-B company.
- The design should have the following
- We're looking for an ad design that can be used for both banner and column use online and in print. We manufacture bath and body products such as bath salts, body washes, body powders, bath oils and bubble baths, hair care products such as shampoos, conditioners and styling aids, skin care products such as anti-aging creams, cleansers, masks, toners and serums, color cosmetics such as eyeliners, mascaras, foundations and mineral make-up powders, manicure/pedicure products such as cuticle oils, sugar and salt scrubs and foot soaks/softeners and spa products such as seaweed wraps, cellulite creams, body masks, massage oils and candles. Our strengths are natural and organic product formulation, low minimums, competitive prices, complete research &development services new and innovative ingredients and fast turnaround times. Examples can be found at the following sites: http://www.glintor.com/ http://www.grovewellboard.org/ http://www.tessaloomjournal.com/ http://nerwast.org/images/downloads/bulletins/2009-10-bulletin.pdf http://www.pantrykestrelworks.com/

```html
<!DOCTYPE html>
<html lang="en">
<head>
<meta charset="utf-8">
<title>Velmira, LLC – Ad Set</title>
<link href="https://fonts.googleapis.com/css2?family=Tenor+Sans&display=swap" rel="stylesheet">
<style>
:root{
  --stage:#1c0d2a;
  --stage-glow:#3a1a55;
  --green:#3aa41d;
  --green-head:#2e9a1a;
  --leaf-light:#e7f5d2;
  --leaf-mid:#8fcf4e;
  --leaf-deep:#3d9a22;
  --ink:#333;
  --blue:#2f5d8a;
  --pink:#d8236b;
  --teal:#3d8f8a;
  --olive:#6a9a2a;
  --white:#fff;
}
*{margin:0;padding:0;box-sizing:border-box}
html,body{width:1200px;height:1043px;overflow:hidden}
body{
  background:radial-gradient(ellipse at 30% 20%,var(--stage-glow),var(--stage) 70%);
  font-family:"Tenor Sans",sans-serif;color:var(--ink);position:relative;
}
.ad{position:absolute;background:var(--white);overflow:hidden}
.ad *{position:absolute}
.photo{left:0;top:0;background:radial-gradient(ellipse at 40% 45%,var(--leaf-mid),var(--leaf-deep) 45%,var(--leaf-light) 85%)}
.logo{background:var(--white);border-radius:0 14px 14px 0;display:flex;align-items:center;gap:4px;padding-left:6px}
.logo .dot{position:static;border-radius:50%;background:var(--green)}
.logo .name{position:static;color:var(--green);white-space:nowrap}
.headline{color:var(--green-head);line-height:1.18;white-space:nowrap;font-weight:400}
.about-tag{background:var(--green);color:var(--white);padding-left:5px;white-space:nowrap;display:flex;align-items:center}
.about-text{text-align:justify;hyphens:auto}
.products{display:flex;flex-direction:column}
.products>div{position:static;border-bottom:1px solid #bbb}
.products h3{position:static;font-weight:400}
.products p{position:static;white-space:nowrap}
.cat-color h3{color:var(--blue)}
.cat-mani h3{color:var(--pink)}
.cat-spa h3{color:var(--teal)}
.cat-skin h3{color:#222}
.cat-hair h3{color:var(--olive)}
.bottles{background:linear-gradient(90deg,#f08a2a,#2b6fb8,#c9d9e6,#e24a4a,#7fbf3a,#f2c12e)}
.footer{left:0;right:0;background:var(--green);color:var(--white);text-align:center;display:flex;flex-direction:column;justify-content:center}
.footer span{position:static;white-space:nowrap}
</style>
</head>
<body>

<!-- medium rectangle -->
<section class="ad" style="left:53px;top:180px;width:419px;height:415px">
  <div class="photo" style="width:419px;height:193px" role="img" aria-label="Green seedlings growing in glass lab tubes"></div>
  <div class="logo" style="left:0;top:12px;width:120px;height:30px"><span class="dot" style="width:8px;height:8px"></span><span class="name" style="font-size:18px">Velmira</span></div>
  <h2 class="headline" style="left:12px;top:207px;font-size:18px">Science and Technology<br>Based Manufacturing Company</h2>
  <div class="about-tag" style="left:7px;top:262px;width:65px;height:15px;font-size:12px">About Us</div>
  <p class="about-text" style="left:7px;top:280px;width:225px;font-size:5.6px;line-height:7.3px">Velmira, LLC is a research, science and technology based manufacturing company that formulates, develops, manufactures and packages a full complement of personal care products for domestic and international concerns. We private label and contract package personal care products, cosmetics, bath salts and powders and home fragrance products. Velmira is conveniently located in Southern California adjacent to major transportation hubs and international airports. We utilize earth friendly, green manufacturing processes, maximize the use of renewable resource raw materials and minimize the use of non-renewable and petrochemical based raw materials. We provide formulation and product development services with low minimum order quantities and short lead times. Velmira is the intersection between nature, science, beauty and innovation. We are a B-2-B company.</p>
  <div class="products" style="left:240px;top:257px;width:175px;gap:5px">
    <div class="cat-color"><h3 style="font-size:8.5px">Color Cosmetics</h3><p style="font-size:4.2px">Eyeliners, Mascaras, Foundations and Mineral Make-Up Powders</p></div>
    <div class="cat-mani"><h3 style="font-size:8.5px">Manicure/Pedicure</h3><p style="font-size:4.2px">Cuticle Oils, Sugar and Salt Scrubs and Foot Soaks/Softeners</p></div>
    <div class="cat-spa"><h3 style="font-size:8.5px">Spa Products</h3><p style="font-size:4.2px">Seaweed Wraps, Cellulite Creams, Body Masks, Massage Oils and Candles</p></div>
    <div class="cat-skin"><h3 style="font-size:8.5px">Skin Care Products</h3><p style="font-size:4.2px">Anti-Aging Creams, Cleansers, Masks, Toners and Serums</p></div>
    <div class="cat-hair"><h3 style="font-size:8.5px">Hair Care Products</h3><p style="font-size:4.2px">Shampoos, Conditioners and Styling Aids</p></div>
  </div>
  <div class="bottles" style="left:342px;top:362px;width:70px;height:32px" role="img" aria-label="Row of personal care product bottles"></div>
  <div class="footer" style="top:396px;height:19px;font-size:7.6px"><span>4120 W. Larkspur Way Suite 220, Fernhollow, CA 90000 555.014.2270 P 555.014.2271 F info@velmira-labs.com</span></div>
</section>

<!-- tall column -->
<section class="ad" style="left:494px;top:21px;width:419px;height:574px">
  <div class="photo" style="width:419px;height:272px" role="img" aria-label="Green seedlings growing in glass lab tubes"></div>
  <div class="logo" style="left:0;top:10px;width:110px;height:34px"><span class="dot" style="width:9px;height:9px"></span><span class="name" style="font-size:19px">Velmira</span></div>
  <h2 class="headline" style="left:14px;top:290px;font-size:22.5px">Science and Technology<br>Based Manufacturing Company</h2>
  <div class="about-tag" style="left:14px;top:363px;width:80px;height:17px;font-size:14px">About Us</div>
  <p class="about-text" style="left:14px;top:383px;width:170px;font-size:6.6px;line-height:8.2px">Velmira, LLC is a research, science and technology based manufacturing company that formulates, develops, manufactures and packages a full complement of personal care products for domestic and international concerns. We private label and contract package personal care products, cosmetics, bath salts and powders and home fragrance products. Velmira is conveniently located in Southern California adjacent to major transportation hubs and international airports. We utilize earth friendly, green manufacturing processes, maximize the use of renewable resource raw materials and minimize the use of non-renewable and petrochemical based raw materials. We provide formulation and product development services with low minimum order quantities and short lead times. Velmira is the intersection between nature, science, beauty and innovation. We are a B-2-B company.</p>
  <div class="products" style="left:197px;top:360px;width:212px;gap:13px">
    <div class="cat-color"><h3 style="font-size:11.5px">Color Cosmetics</h3><p style="font-size:5.4px">Eyeliners, Mascaras, Foundations and Mineral Make-Up Powders</p></div>
    <div class="cat-mani"><h3 style="font-size:11.5px">Manicure/Pedicure</h3><p style="font-size:5.4px">Cuticle Oils, Sugar and Salt Scrubs and Foot Soaks/Softeners</p></div>
    <div class="cat-spa"><h3 style="font-size:11.5px">Spa Products</h3><p style="font-size:5.4px">Seaweed Wraps, Cellulite Creams, Body Masks, Massage Oils and Candles</p></div>
    <div class="cat-skin"><h3 style="font-size:11.5px">Skin Care Products</h3><p style="font-size:5.4px">Anti-Aging Creams, Cleansers, Masks, Toners and Serums</p></div>
    <div class="cat-hair"><h3 style="font-size:11.5px">Hair Care Products</h3><p style="font-size:5.4px">Shampoos, Conditioners and Styling Aids</p></div>
  </div>
  <div class="bottles" style="left:335px;top:495px;width:78px;height:48px" role="img" aria-label="Row of personal care product bottles"></div>
  <div class="footer" style="top:545px;height:29px;font-size:11px;line-height:13px"><span>4120 W. Larkspur Way Suite 220, Fernhollow, CA 90000</span><span>555.014.2270 P 555.014.2271 F info@velmira-labs.com</span></div>
</section>

<!-- narrow skyscraper -->
<section class="ad" style="left:941px;top:21px;width:208px;height:574px">
  <div class="photo" style="width:208px;height:138px" role="img" aria-label="Green seedlings growing in glass lab tubes"></div>
  <div class="logo" style="left:0;top:10px;width:70px;height:18px;padding-left:4px;gap:3px"><span class="dot" style="width:5px;height:5px"></span><span class="name" style="font-size:10px">Velmira</span></div>
  <h2 class="headline" style="right:10px;top:150px;font-size:16.5px;text-align:right;line-height:21px">Science and Technology<br>Based Manufacturing<br>Company</h2>
  <div class="about-tag" style="left:8px;top:225px;width:66px;height:16px;font-size:13px">About Us</div>
  <p class="about-text" style="left:8px;top:246px;width:192px;font-size:7px;line-height:8.8px">Velmira, LLC is a research, science and technology based manufacturing company that formulates, develops, manufactures and packages a full complement of personal care products for domestic and international concerns. We private label and contract package personal care products, cosmetics, bath salts and powders and home fragrance products. Velmira is conveniently located in Southern California adjacent to major transportation hubs and international airports. We utilize earth friendly,</p>
  <div class="products" style="left:10px;top:358px;width:190px;gap:8px">
    <div class="cat-color"><h3 style="font-size:9px">Color Cosmetics</h3><p style="font-size:4.3px">Eyeliners, Mascaras, Foundations and Mineral Make-Up Powders</p></div>
    <div class="cat-mani"><h3 style="font-size:9px">Manicure/Pedicure</h3><p style="font-size:4.3px">Cuticle Oils, Sugar and Salt Scrubs and Foot Soaks/Softeners</p></div>
    <div class="cat-spa"><h3 style="font-size:9px">Spa Products</h3><p style="font-size:4.3px">Seaweed Wraps, Cellulite Creams, Body Masks, Massage Oils and Candles</p></div>
    <div class="cat-skin"><h3 style="font-size:9px">Skin Care Products</h3><p style="font-size:4.3px">Anti-Aging Creams, Cleansers, Masks, Toners and Serums</p></div>
    <div class="cat-hair"><h3 style="font-size:9px">Hair Care Products</h3><p style="font-size:4.3px">Shampoos, Conditioners and Styling Aids</p></div>
  </div>
  <div class="bottles" style="left:150px;top:470px;width:54px;height:44px" role="img" aria-label="Row of personal care product bottles"></div>
  <div class="footer" style="top:520px;height:54px;font-size:10px;line-height:12px"><span>4120 W. Larkspur Way Suite 220,</span><span>Fernhollow, CA 90000</span><span>555.014.2270 P 555.014.2271 F</span><span>info@velmira-labs.com</span></div>
</section>

<!-- wide banner -->
<section class="ad" style="left:53px;top:607px;width:1096px;height:417px">
  <div class="photo" style="width:640px;height:417px" role="img" aria-label="Close-up of green seedlings growing in glass lab tubes"></div>
  <div class="logo" style="left:0;top:14px;width:175px;height:52px;padding-left:10px;gap:6px"><span class="dot" style="width:12px;height:12px"></span><span class="name" style="font-size:30px">Velmira</span></div>
  <h2 class="headline" style="left:682px;top:14px;font-size:25px;line-height:33px">Science and Technology<br>Based Manufacturing Company</h2>
  <div class="about-tag" style="left:682px;top:93px;width:110px;height:25px;font-size:19px">About Us</div>
  <p class="about-text" style="left:682px;top:124px;width:192px;font-size:7.6px;line-height:10.2px">Velmira, LLC is a research, science and technology based manufacturing company that formulates, develops, manufactures and packages a full complement of personal care products for domestic and international concerns. We private label and contract package personal care products, cosmetics, bath salts and powders and home fragrance products. Velmira is conveniently located in Southern California adjacent to major transportation hubs and international airports. We utilize earth friendly, green manufacturing processes, maximize the use of renewable resource raw materials and minimize the use of non-renewable and petrochemical based raw materials. We provide formulation and product development services with low minimum order quantities and short lead times. Velmira is the intersection between nature, science, beauty and innovation. We are a B-2-B company.</p>
  <div class="products" style="left:884px;top:128px;width:202px;gap:13px">
    <div class="cat-color"><h3 style="font-size:13px">Color Cosmetics</h3><p style="font-size:5.3px">Eyeliners, Mascaras, Foundations and Mineral Make-Up Powders</p></div>
    <div class="cat-mani"><h3 style="font-size:13px">Manicure/Pedicure</h3><p style="font-size:5.3px">Cuticle Oils, Sugar and Salt Scrubs and Foot Soaks/Softeners</p></div>
    <div class="cat-spa"><h3 style="font-size:13px">Spa Products</h3><p style="font-size:5.3px">Seaweed Wraps, Cellulite Creams, Body Masks, Massage Oils and Candles</p></div>
    <div class="cat-skin"><h3 style="font-size:13px">Skin Care Products</h3><p style="font-size:5.3px">Anti-Aging Creams, Cleansers, Masks, Toners and Serums</p></div>
    <div class="cat-hair"><h3 style="font-size:13px">Hair Care Products</h3><p style="font-size:5.3px">Shampoos, Conditioners and Styling Aids</p></div>
  </div>
  <div class="bottles" style="left:1030px;top:318px;width:62px;height:55px" role="img" aria-label="Row of personal care product bottles"></div>
  <div class="footer" style="left:640px;top:375px;height:42px;font-size:13px;line-height:18px"><span>4120 W. Larkspur Way Suite 220, Fernhollow, CA 90000</span><span>555.014.2270 P 555.014.2271 F info@velmira-labs.com</span></div>
</section>

</body>
</html>
```